Pinecrest Capital Group - Company Envelopes

I am looking for a graphic designer to create a bespoke envelope for my company use, which I can then have printed at scale. The envelope should be of standard size and shape, but Matt black in colour, with semi-thick vertical gloss (shiny) lines going from left to right, but must stop to the right of the envelope, leaving a Matt black line with enough space for a stamp in the top right corner. The back of the envelope should be full Matt black.

Requirements
Must have
• Must be as described in brief
Should not have
• No other colours - Just Matt and Gloss Black

```html
<!DOCTYPE html>
<html lang="en">
<head>
<meta charset="utf-8">
<title>Pinecrest Capital Group – Envelope Front</title>
<link rel="stylesheet" href="https://fonts.googleapis.com/css2?family=EB+Garamond:wght@600&display=swap">
<style>
  :root {
    --matte-black: #050505;
    --matte-black-soft: #0d0d0d;
    --gloss-black-edge: #0a0a0a;
    --gloss-black-shine: #232323;
    --brand-white: #ffffff;
  }
  * { margin: 0; padding: 0; box-sizing: border-box; }
  html, body {
    width: 1200px;
    height: 863px;
    overflow: hidden;
    background: var(--matte-black);
  }
  .envelope {
    position: relative;
    width: 1200px;
    height: 863px;
    overflow: hidden;
    background:
      radial-gradient(ellipse at 20% 15%, var(--matte-black-soft) 0%, transparent 60%),
      var(--matte-black);
  }
  .gloss-stripes {
    position: absolute;
    top: 0;
    left: 0;
    width: 1010px;
    height: 100%;
    background: repeating-linear-gradient(
      to right,
      var(--gloss-black-edge) 0px,
      var(--gloss-black-shine) 11px,
      var(--gloss-black-edge) 22px,
      transparent 22px,
      transparent 44px
    );
    opacity: 0.9;
  }
  .stamp-band {
    position: absolute;
    top: 0;
    right: 0;
    width: 190px;
    height: 100%;
    background: var(--matte-black);
  }
  .brand {
    position: absolute;
    left: 331px;
    top: 72px;
    width: 538px;
    height: 123px;
    display: flex;
    align-items: center;
    justify-content: center;
  }
  .brand-name {
    font-family: "EB Garamond", "Times New Roman", serif;
    font-weight: 600;
    font-size: 37px;
    color: var(--brand-white);
    text-transform: uppercase;
    white-space: nowrap;
    line-height: 1;
  }
</style>
</head>
<body>
  <main class="envelope">
    <div class="gloss-stripes" aria-hidden="true"></div>
    <div class="stamp-band" aria-hidden="true"></div>
    <header class="brand">
      <span class="brand-name">Pinecrest Capital Group</span>
    </header>
  </main>
</body>
</html>
```